Pediatric Speech Therapy Private Practice Announcement

I opened a solo private practice as a pediatric speech therapist in June 2014 in Orinda, CA in June 2014. I have 25 years experience in the field and worked as the Director of a very successful group practice of speech therapists in nearby Walnut Creek. I am trying to get my own name established in the local community and letting people know that I now have my own practice, which I call Dalworth Speech-Language Center.

I would like this postcard to advertise low-cost speech-language screenings offered to nearby preschools.

Target Market(s)

Preschool Directors

Requirements
Must have
• Photos of children, preschool ages, 3-5

Bright colors to get attention

```html
<!DOCTYPE html>
<html lang="en">
<head>
<meta charset="utf-8">
<title>Dalworth Speech-Language Center – Postcard</title>
<link rel="stylesheet" href="https://fonts.googleapis.com/css2?family=Arimo:wght@400;700&family=Jost:ital,wght@0,400;0,700;0,800;1,600;1,700;1,800&display=swap">
<style>
:root{
  --backdrop:#5b5b5b;
  --paper:#ffffff;
  --teal:#0f6a8b;
  --magenta:#d3137b;
  --navy:#1d2a57;
  --orange:#f07b1c;
  --mint:#18a596;
  --yellow:#fff200;
  --band-yellow:#f6ec3a;
}
*{margin:0;padding:0;box-sizing:border-box}
html,body{width:1200px;height:815px;overflow:hidden;background:var(--backdrop)}
.canvas{position:relative;width:1200px;height:815px}
.postcard{position:absolute;left:60px;top:60px;width:1080px;height:695px;background:var(--paper);overflow:hidden;font-family:"Jost",Arial,sans-serif}
.headline{position:absolute;left:32px;top:26px;z-index:2;font-weight:800;font-style:italic;font-size:50px;line-height:52px;text-transform:uppercase;letter-spacing:0}
.headline .teal{color:var(--teal)}
.headline .magenta{color:var(--magenta)}
.kids-photo{position:absolute;left:0;top:140px;width:480px;height:440px;background:radial-gradient(ellipse at 50% 55%,#f4c9a8 0%,#e9a07a 30%,#f7f3f0 70%,#fff 100%)}
.intro{position:absolute;left:488px;top:172px;width:262px;font-weight:700;font-style:italic;font-size:16px;line-height:23px;color:var(--navy)}
.cta{position:absolute;left:480px;top:390px;width:280px;text-align:center;font-style:italic;font-weight:700}
.cta-call{color:var(--orange);font-size:26px;line-height:34px}
.cta-phone{color:var(--magenta);font-size:35px;line-height:42px;font-weight:800}
.cta-note{color:var(--navy);font-size:15.5px;line-height:21px;margin-top:6px}
.cta-note em{color:var(--magenta)}
.web{position:absolute;left:292px;top:548px;font-weight:700;font-style:italic;font-size:19.5px;letter-spacing:.5px;color:var(--mint)}
.brand-band{position:absolute;left:0;top:580px;width:1080px;height:115px;background:var(--magenta)}
.brand-name{position:absolute;left:52px;top:10px;color:#fff;font-family:"Arimo",Arial,sans-serif;font-weight:400;font-size:39px;line-height:46px}
.brand-services{position:absolute;left:52px;top:57px;color:var(--band-yellow);font-family:"Arimo",Arial,sans-serif;font-size:23.5px;line-height:28px}
.snapshot{position:absolute;background:var(--paper);padding:9px;box-shadow:2px 3px 8px rgba(0,0,0,.35)}
.snapshot .shot{width:100%;height:100%}
.snap-1{left:865px;top:-10px;width:220px;height:195px;transform:rotate(4deg)}
.snap-1 .shot{background:linear-gradient(135deg,#c9d8cf,#7d9bb0 55%,#c4563b)}
.snap-2{left:772px;top:150px;width:270px;height:210px;transform:rotate(2deg)}
.snap-2 .shot{background:linear-gradient(120deg,#f2c5a6,#d94d5a 45%,#e9e2cf)}
.snap-3{left:795px;top:315px;width:275px;height:220px;transform:rotate(7deg)}
.snap-3 .shot{background:linear-gradient(120deg,#e94a4f,#f3c9ae 50%,#f2c2d8)}
.price-badge{position:absolute;left:865px;top:485px;width:190px;height:190px}
.price-text{position:absolute;left:865px;top:485px;width:190px;height:190px;text-align:center;color:var(--navy);font-family:"Arimo",Arial,sans-serif}
.price-only{position:absolute;top:24px;width:100%;font-weight:700;font-size:19px;line-height:22px}
.price-amount{position:absolute;top:44px;width:100%;color:var(--orange);font-weight:700;font-size:64px;line-height:70px}
.price-amount small{font-size:32px;font-weight:400}
.price-label{position:absolute;top:113px;width:100%;font-size:14px;line-height:16px}
</style>
</head>
<body>
<main class="canvas">
  <article class="postcard">
    <div class="kids-photo" role="img" aria-label="Group of smiling preschool children sitting together in colourful clothes"></div>

    <figure class="snapshot snap-1"><div class="shot" role="img" aria-label="Teacher reading a picture book to a preschool class"></div></figure>
    <figure class="snapshot snap-2"><div class="shot" role="img" aria-label="Therapist playing with a young girl at a table"></div></figure>
    <figure class="snapshot snap-3"><div class="shot" role="img" aria-label="Therapist and toddler playing with a toy"></div></figure>

    <h1 class="headline">
      <span class="teal">New</span> <span class="magenta">Pediatric Speech</span><br>
      <span class="magenta">Therapy</span> <span class="teal">Practice in Orinda</span>
    </h1>

    <p class="intro">Dalworth Speech-Language Center, a new speech therapy practice in Orinda owned by Maren Holt, MS, CCC-SLP, is offering low cost ($40) on site speech-language screenings at preschools this Fall in the Lamorinda area.</p>

    <div class="cta">
      <p class="cta-call">Call Today!!</p>
      <p class="cta-phone">(925) 555-0148</p>
      <p class="cta-note">for additional information, or to schedule an <em>on-site screening</em> at your preschool today!</p>
    </div>

    <p class="web">www.dalworthspeech-languagecenter.com</p>

    <footer class="brand-band">
      <p class="brand-name">Dalworth Speech-Language Center</p>
      <p class="brand-services">Speech, Language, and Social Communication Therapy Services</p>
    </footer>

    <svg class="price-badge" viewBox="0 0 200 200" aria-hidden="true">
      <circle cx="100" cy="100" r="100" fill="#fff"/>
      <circle cx="100" cy="100" r="84" fill="var(--yellow)"/>
      <circle cx="100" cy="100" r="89" fill="none" stroke="var(--yellow)" stroke-width="10" stroke-dasharray="11 8"/>
    </svg>
    <div class="price-text">
      <p class="price-only">ONLY</p>
      <p class="price-amount">40<small>$</small></p>
      <p class="price-label">SPEECH-LANGUAGE<br>SCREENING</p>
    </div>
  </article>
</main>
</body>
</html>
```